Logistics Website Design

See website https://tqfreightglobal.com for theme and color details. Need the site to be re-done and reflect some of the designs shown in this list here: https://pixelvane.com/tags/logistics-company-website

Target Market(s)

Logistics & Transportation

Industry/Entity Type

Logistics and Supply Chain

Coding

Number of Pages Required

5+ page

Requirements
Must have
• Colors must match theme of logo. Looking for a sleek, interactive design.

```html
<!DOCTYPE html>
<html lang="en">
<head>
<meta charset="utf-8">
<title>TQ Freight Global — Logistics</title>
<link rel="stylesheet" href="https://fonts.googleapis.com/css2?family=Poppins:wght@300;400;500;600;700&display=swap">
<style>
:root{
  --ink:#0f1217;
  --navy:#161b24;
  --card:#16181d;
  --orange:#ef6a3a;
  --orange-deep:#d9542a;
  --white:#ffffff;
  --paper:#ffffff;
  --muted:#c9ccd2;
  --text-dark:#1b1b1b;
  --grey-text:#4a4a4a;
  --line:rgba(255,255,255,.18);
}
*{box-sizing:border-box;margin:0;padding:0}
html,body{width:1200px;height:4234px;overflow:hidden}
body{font-family:"Poppins",sans-serif;background:var(--ink);color:var(--white);position:relative}
.btn{position:absolute;display:flex;align-items:center;justify-content:center;background:var(--orange);color:var(--white);font-weight:600;font-size:14px;letter-spacing:.3px;clip-path:polygon(6% 0,100% 0,94% 100%,0 100%)}
.rule{position:absolute;height:2px;background:linear-gradient(90deg,transparent,var(--orange),transparent)}

/* hero */
.hero{position:absolute;left:0;top:0;width:1200px;height:1452px;background:linear-gradient(180deg,#23272e 0%,#1a1e25 30%,#12161d 60%,#0c0f14 100%)}
.nav a{position:absolute;top:60px;color:var(--white);font-size:15px;text-decoration:none}
.nav .active{font-weight:600}
.brand{position:absolute;display:flex;align-items:center;gap:8px;color:var(--white);font-weight:600}
.brand i{display:block;border-radius:50%;background:var(--orange)}
.hero h1{position:absolute;left:110px;top:182px;font-size:56px;line-height:64px;font-weight:600}
.hero-card{position:absolute;left:723px;top:186px;width:367px;height:144px;border:1px solid var(--line);border-radius:8px;background:rgba(20,24,31,.6);padding:28px 38px}
.hero-card p{font-size:15px;line-height:26px;color:#e6e6e6}
.hero-card span{display:block;margin-top:10px;color:var(--orange);font-weight:600;font-size:14px}
.truck-art{position:absolute;left:99px;top:391px;width:1035px;height:283px;border-radius:4px;background:linear-gradient(90deg,#a9532d 0%,#c56a3b 35%,#b8855a 50%,#c86a3a 70%,#d66a30 100%)}
.hero h2{position:absolute;left:0;width:1200px;top:762px;text-align:center;font-size:58px;font-weight:600}
.svc{position:absolute;top:909px;width:237px;height:405px;border:1px solid #3a3d44;border-radius:10px;background:var(--card);text-align:center;padding:52px 16px 0}
.svc.on{background:linear-gradient(180deg,#f07b4e,#ec6a3b);border-color:var(--orange)}
.svc h3{font-size:20px;line-height:26px;font-weight:500;margin-top:22px}
.svc p{font-size:13px;line-height:26.5px;margin-top:22px;color:#e8e8e8}

/* about */
.about{position:absolute;left:0;top:1452px;width:1200px;height:833px;background:linear-gradient(135deg,#f3f3f3,#ffffff 50%,#f4f4f4)}
.about h2{position:absolute;left:110px;top:132px;font-size:55px;line-height:63px;font-weight:600;color:var(--text-dark)}
.about p{position:absolute;left:112px;top:385px;width:440px;font-size:15.5px;line-height:27.5px;color:var(--grey-text);font-weight:300}
.globe{position:absolute;left:616px;top:77px;width:584px;height:608px;border-radius:50%;background:radial-gradient(circle at 50% 50%,#f6d8cb 0%,#f4e3dc 55%,rgba(255,255,255,0) 72%)}

/* industries */
.industries{position:absolute;left:0;top:2285px;width:1200px;height:932px;background:var(--paper)}
.ind-h{position:absolute;left:112px;top:109px;font-size:55px;line-height:63px;font-weight:600;color:var(--text-dark)}
.tile{position:absolute;width:312px;height:381px;border-radius:2px;padding-top:48px;text-align:center;font-size:20px;line-height:29px;font-weight:500;color:var(--white)}
.t-food{left:444px;top:5px;background:linear-gradient(180deg,#6a5547,#9a3a2e 55%,#4a4036)}
.t-retail{left:776px;top:5px;background:linear-gradient(180deg,#7b6e65,#4a3c36 55%,#2d2a2c)}
.t-mfg{left:112px;top:405px;background:linear-gradient(180deg,#2c3446,#6c7fa8 55%,#3a2a22)}
.t-pharma{left:444px;top:405px;background:linear-gradient(180deg,#5a6b7d,#8aa6c6 50%,#6f8fb2)}
.t-gov{left:776px;top:405px;background:linear-gradient(180deg,#3c4a5c,#a79a86 55%,#6a5436)}

/* contact */
.contact{position:absolute;left:0;top:3217px;width:1200px;height:1017px;background:linear-gradient(180deg,#1c1f24,#14171c 60%,#0f1114)}
.contact h2{position:absolute;left:112px;top:155px;font-size:56px;font-weight:600}
.contact .lead{position:absolute;left:112px;top:258px;width:330px;font-size:14.5px;line-height:25px;color:#e4e4e4}
.info{position:absolute;left:112px;display:flex;gap:18px;font-size:17px;line-height:27px;align-items:flex-start}
.form{position:absolute;left:589px;top:96px;width:501px;height:526px;border:1px solid #4a4e55;border-radius:14px;background:rgba(60,64,72,.55)}
.form h3{position:absolute;left:0;width:100%;top:40px;text-align:center;font-size:21px;font-weight:500}
.field{position:absolute;left:52px;width:396px;height:52px;border:1px solid #5a5d63;border-radius:6px;background:#15171b;padding:14px 20px;font-size:14px;color:#e8e8e8}
.foot-links{position:absolute;right:112px;top:4050px;display:flex;gap:24px;font-size:17px}
.copy{position:absolute;right:112px;top:4101px;font-size:16.5px}
</style>
</head>
<body>

<section class="hero">
  <nav class="nav">
    <a class="active" style="left:110px">Home</a>
    <a style="left:180px">Services</a>
    <a style="left:272px">Industries</a>
    <a style="left:377px">About Us</a>
    <a style="left:787px">Contact Us</a>
  </nav>
  <div class="brand" style="left:532px;top:62px;font-size:16px"><i style="width:14px;height:14px"></i>TQ Freight Global</div>
  <div class="btn" style="left:900px;top:46px;width:190px;height:45px">REQUEST A QUOTE</div>

  <h1>Delivering Strength<br>in Every Mile</h1>
  <div class="rule" style="left:145px;top:334px;width:120px"></div>
  <div class="hero-card">
    <p>Secure and reliable transportation for all your cargo needs.</p>
    <span>REQUEST A QUOTE &nbsp;→</span>
  </div>
  <div class="truck-art" role="img" aria-label="Orange semi-truck with open cargo container loaded with boxes, in a warehouse"></div>

  <h2>Our Services</h2>
  <div class="rule" style="left:515px;top:843px;width:170px"></div>

  <div class="svc" style="left:110px">
    <svg width="110" height="60" viewBox="0 0 110 60" fill="none" stroke="#ef6a3a" stroke-width="3"><path d="M4 38h60M20 38v4M70 18h14l8 12v10H70zM64 30v10h6M76 8v10"/><circle cx="20" cy="46" r="5"/><circle cx="56" cy="46" r="5"/><circle cx="82" cy="46" r="5"/></svg>
    <h3>Flatbed<br>Transportation</h3>
    <p>From routine shipments to oversized and heavy-haul loads, we handle freight requiring proper securement, regulatory knowledge, and consistent on-time execution.</p>
  </div>
  <div class="svc on" style="left:358px">
    <svg width="100" height="60" viewBox="0 0 100 60" fill="#fff"><rect x="22" y="4" width="14" height="12"/><rect x="10" y="18" width="40" height="12"/><rect x="6" y="32" width="70" height="8"/><path d="M72 14h14l8 12v14H72z"/><circle cx="20" cy="50" r="7"/><circle cx="40" cy="50" r="7"/><circle cx="60" cy="50" r="7"/><circle cx="84" cy="50" r="7"/></svg>
    <h3>Step Deck<br>Transportation</h3>
    <p>Our step deck trucking services support tall, heavy, and specialized freight that requires additional height clearance and flexible loading options.</p>
  </div>
  <div class="svc" style="left:605px">
    <svg width="110" height="60" viewBox="0 0 110 60" fill="#ef6a3a"><rect x="6" y="6" width="70" height="34" rx="2"/><path d="M80 16h14l10 12v12H80z"/><circle cx="20" cy="48" r="6"/><circle cx="36" cy="48" r="6"/><circle cx="92" cy="48" r="6"/></svg>
    <h3>Dry Van<br>Transportation</h3>
    <p>From consumer goods to industrial materials, our dry van services provide the space, security, and consistency you need coast to coast.</p>
  </div>
  <div class="svc" style="left:853px">
    <svg width="60" height="60" viewBox="0 0 60 60" fill="none" stroke="#ef6a3a" stroke-width="3"><rect x="10" y="6" width="40" height="40" rx="3"/><rect x="16" y="12" width="28" height="12"/><path d="M16 32h28M16 38h28"/><rect x="12" y="46" width="8" height="8"/><rect x="40" y="46" width="8" height="8"/></svg>
    <h3>Heavy Haul<br>Transportation</h3>
    <p>We provide heavy haul trucking solutions for oversized, overweight, and over-dimensional freight.</p>
  </div>
</section>

<section class="about">
  <h2>Keeping Your<br>Supply Chain<br>Moving</h2>
  <div class="rule" style="left:112px;top:340px;width:190px"></div>
  <p>We deliver a comprehensive range of open-deck and specialized transportation services—including flatbed, step deck, heavy haul, and over-dimensional freight solutions. Backed by years of experience, a trusted nationwide carrier network, and a strong safety-first culture, we provide reliable, adaptable logistics support built around the unique requirements of every load.</p>
  <div class="btn" style="left:112px;top:616px;width:190px;height:45px">LEARN MORE</div>
  <div class="globe" role="img" aria-label="Orange world globe with connected network routes"></div>
</section>

<section class="industries">
  <h2 class="ind-h">Industries<br>We Serve</h2>
  <div class="rule" style="left:112px;top:264px;width:170px"></div>
  <div class="tile t-food" role="img" aria-label="Crate of red apples in a warehouse">Food &amp; Beverage</div>
  <div class="tile t-retail" role="img" aria-label="Retail store worker with a tablet">E-Commerce<br>&amp; Retail</div>
  <div class="tile t-mfg" role="img" aria-label="Welder with sparks in a factory">Manufacturing</div>
  <div class="tile t-pharma" role="img" aria-label="Stacked pharmaceutical boxes">Pharma &amp; Healthcare</div>
  <div class="tile t-gov" role="img" aria-label="Box truck being loaded with cartons">Government Secured<br>Freight</div>
</section>

<section class="contact">
  <h2>Get in Touch</h2>
  <div class="rule" style="left:112px;top:225px;width:120px"></div>
  <p class="lead">Let's discuss your logistics needs and how we can help your business thrive</p>
  <div class="info" style="top:353px"><svg width="24" height="24" viewBox="0 0 24 24" fill="none" stroke="#fff" stroke-width="1.6"><path d="M5 3h4l2 5-3 2a12 12 0 0 0 6 6l2-3 5 2v4a2 2 0 0 1-2 2A18 18 0 0 1 3 5a2 2 0 0 1 2-2z"/></svg>3015550142</div>
  <div class="info" style="top:402px"><svg width="24" height="24" viewBox="0 0 24 24" fill="none" stroke="#fff" stroke-width="1.6"><rect x="2" y="5" width="20" height="14"/><path d="M2 5l10 8 10-8"/></svg>sales@tqfreightglobal.com</div>
  <div class="info" style="top:445px"><svg width="24" height="24" viewBox="0 0 24 24" fill="none" stroke="#fff" stroke-width="1.6"><path d="M12 22s7-7 7-12a7 7 0 0 0-14 0c0 5 7 12 7 12z"/><circle cx="12" cy="10" r="2.5"/></svg>TQ Freight Global,<br>Address comes here</div>

  <div class="form">
    <h3>Let’s Move Your Business Forward</h3>
    <div class="field" style="top:124px">Full Name</div>
    <div class="field" style="top:186px">Email</div>
    <div class="field" style="top:248px">Phone</div>
    <div class="field" style="top:310px;height:100px">Message</div>
    <div class="btn" style="left:159px;top:435px;width:186px;height:45px">SEND NOW</div>
  </div>
</section>

<div class="brand" style="left:112px;top:4076px;font-size:20px"><i style="width:18px;height:18px"></i>TQ Freight Global</div>
<div class="foot-links"><span>Home</span><span>Services</span><span>Industries</span><span>About Us</span><span>Contact Us</span></div>
<div class="copy">2026 TQ Freight Global. Alle Rechte vorbehalten.</div>

</body>
</html>
```